Stationery Design Project for Nimbora, Chicago

Nimbora, a street parking application which helps car drivers find a street parking spot by offering an ideal path along which to look for parking. This path is calculated by our algorithm based on data (e.g. historical data, baseball games schedule, etc.). Along this path the driver will find a spot and will also save 70% of the search time. Customer we target is reg. between 21 and 45 yo.

We envision something young, fresh, bright and original. Slightly abstract maybe. It should represent the idea and elements of finding street parking in the city, e.g. car(s), parking spot, people, city, etc. (just ideas!).

Logo is attached.

Requirement:
- Business Cards (2 Sided Full Color CMYK)
- Letterhead (1 Sided Full Color CMYK)
- Envelope (1 Sided Full Color CMYK)
- Sticker (1 Sided Full Color CMYK), round with a 2inch diameter.

Reason: We're starting to get more and more designs and need more time to look into all of them. Very exciting!! Thanks to everybody!

Hi all, we're in the process of selecting our favs. Though choices!!! Really good submissions. Will keep you posted and sorry for the delay.

Target Market(s)

Car drivers and owners between 21 and 45

Industry/Entity Type

Parking

Requirements
Must have
• Sticker should be round and include company URL nimbora.com and the new logo which we will attach soon.
Should not have
• Should not be too serious or boring.

```html
<!DOCTYPE html>
<html lang="en">
<head>
<meta charset="utf-8">
<title>Nimbora Business Card</title>
<link rel="stylesheet" href="https://fonts.googleapis.com/css2?family=Open+Sans:wght@400;600;700&display=swap">
<style>
  :root {
    --backdrop: #b78f2a;
    --card: #ffffff;
    --ink: #2a2a2a;
    --ink-soft: #3a3a3a;
    --accent: #1592d6;
    --brand-blue: #1c63c0;
    --divider: #4a4a4a;
  }
  html, body {
    margin: 0;
    padding: 0;
    width: 1200px;
    height: 686px;
    overflow: hidden;
    background: var(--backdrop);
    font-family: "Open Sans", Arial, sans-serif;
  }
  .canvas {
    position: relative;
    width: 1200px;
    height: 686px;
  }
  .card {
    position: absolute;
    width: 449px;
    height: 257px;
    background: var(--card);
    border-radius: 17px;
    overflow: hidden;
  }
  .card--front { left: 127px; top: 133px; }
  .card--back { left: 620px; top: 284px; }

  .brand {
    position: absolute;
    display: flex;
    align-items: center;
  }
  .brand__dot {
    border-radius: 50%;
    background: var(--brand-blue);
    flex: none;
  }
  .brand__name {
    font-weight: 600;
    color: var(--ink);
    letter-spacing: 0.5px;
    line-height: 1;
  }
  .card--front .brand { left: 101px; top: 35px; gap: 11px; }
  .card--front .brand__dot { width: 76px; height: 76px; }
  .card--front .brand__name { font-size: 40px; }
  .card--back .brand { left: 79px; top: 79px; gap: 12px; }
  .card--back .brand__dot { width: 84px; height: 84px; }
  .card--back .brand__name { font-size: 46px; }

  .identity {
    position: absolute;
    right: calc(449px - 205px);
    top: 131px;
    text-align: right;
    color: var(--ink-soft);
    font-size: 13px;
    line-height: 16px;
  }
  .identity__name {
    color: var(--accent);
    font-weight: 700;
    font-size: 16px;
    line-height: 20px;
  }
  .identity__title {
    color: #000;
    font-weight: 700;
    font-size: 13px;
    line-height: 17px;
    margin-bottom: 8px;
  }
  .divider {
    position: absolute;
    left: 222px;
    top: 137px;
    width: 1px;
    height: 67px;
    background: var(--divider);
  }
  .contacts {
    position: absolute;
    left: 244px;
    top: 135px;
    margin: 0;
    padding: 0;
    list-style: none;
    font-size: 13px;
    color: var(--ink-soft);
  }
  .contacts li {
    display: flex;
    align-items: center;
    gap: 5px;
    height: 18px;
    margin-bottom: 1px;
  }
  .contacts li:first-child { margin-bottom: 3px; }
  .contacts svg { width: 11px; height: 11px; flex: none; fill: var(--accent); }

  .band {
    position: absolute;
    left: 0;
    bottom: 0;
    width: 449px;
    height: 26px;
    display: block;
  }
</style>
</head>
<body>
<main class="canvas">

  <section class="card card--front" aria-label="Business card front">
    <div class="brand">
      <span class="brand__dot"></span>
      <span class="brand__name">Nimbora</span>
    </div>

    <div class="identity">
      <div class="identity__name">Your Name</div>
      <div class="identity__title">Title</div>
      <div>Street name City</div>
      <div>State, zip code</div>
    </div>

    <div class="divider"></div>

    <ul class="contacts">
      <li>
        <svg viewBox="0 0 12 12" aria-hidden="true"><path d="M2.3 0.8l1.8 0 0.8 2.6-1.2 0.9c0.6 1.5 1.6 2.6 3 3.2l0.9-1.2 2.6 0.8 0 1.8c0 0.7-0.6 1.3-1.3 1.3C5 10.2 1.8 7 1 2.1 1 1.4 1.6 0.8 2.3 0.8z"/></svg>
        123-456-7890
      </li>
      <li>
        <svg viewBox="0 0 12 12" aria-hidden="true"><path d="M3 0h5l1 1v2H3z M1 4h10v6H9V8H3v2H1z M3.5 9h5v3h-5z"/></svg>
        123-456-7890
      </li>
      <li>
        <svg viewBox="0 0 12 12" aria-hidden="true"><path d="M0 2h12v1L6 7 0 3z M0 4.3l6 4 6-4V10H0z"/></svg>
        name@website.com
      </li>
      <li>
        <svg viewBox="0 0 12 12" aria-hidden="true"><circle cx="6" cy="6" r="5.2" fill="none" stroke="#1592d6" stroke-width="1.2"/><ellipse cx="6" cy="6" rx="2.2" ry="5.2" fill="none" stroke="#1592d6" stroke-width="1"/><path d="M1 6h10" stroke="#1592d6" stroke-width="1"/></svg>
        www.website.com
      </li>
    </ul>

    <svg class="band" viewBox="0 0 449 26" preserveAspectRatio="none" aria-hidden="true">
      <defs>
        <linearGradient id="bandBlueFront" x1="0" x2="1" y1="0" y2="0">
          <stop offset="0" stop-color="#1b58ab"/>
          <stop offset="0.5" stop-color="#0d8fd6"/>
          <stop offset="1" stop-color="#00c0f5"/>
        </linearGradient>
        <linearGradient id="bandGreyFront" x1="0" x2="1" y1="0" y2="0">
          <stop offset="0" stop-color="#8a8a8a"/>
          <stop offset="0.5" stop-color="#3a3a3a"/>
          <stop offset="1" stop-color="#050505"/>
        </linearGradient>
      </defs>
      <rect x="320" y="0" width="129" height="26" fill="url(#bandGreyFront)"/>
      <path d="M0 0H344Q337 18 324 26H0Z" fill="url(#bandBlueFront)" stroke="#fff" stroke-width="3"/>
    </svg>
  </section>

  <section class="card card--back" aria-label="Business card back">
    <div class="brand">
      <span class="brand__dot"></span>
      <span class="brand__name">Nimbora</span>
    </div>

    <svg class="band" viewBox="0 0 449 26" preserveAspectRatio="none" aria-hidden="true">
      <defs>
        <linearGradient id="bandBlueBack" x1="0" x2="1" y1="0" y2="0">
          <stop offset="0" stop-color="#1b58ab"/>
          <stop offset="0.5" stop-color="#0d8fd6"/>
          <stop offset="1" stop-color="#00c0f5"/>
        </linearGradient>
        <linearGradient id="bandGreyBack" x1="0" x2="1" y1="0" y2="0">
          <stop offset="0" stop-color="#8a8a8a"/>
          <stop offset="0.5" stop-color="#3a3a3a"/>
          <stop offset="1" stop-color="#050505"/>
        </linearGradient>
      </defs>
      <rect x="320" y="0" width="129" height="26" fill="url(#bandGreyBack)"/>
      <path d="M0 0H344Q337 18 324 26H0Z" fill="url(#bandBlueBack)" stroke="#fff" stroke-width="3"/>
    </svg>
  </section>

</main>
</body>
</html>
```